Need a FLAT UI design for mobile campus Marketplace APP

We need to improve our current UI/UX design for a mobile application called Tradolo. It is designed for students to buy and sell their goods, such as books and furnitures, on their own campus to save living expenses. Our initial design does not look very flat and clear enough. We would like to see a flat design improvement for a better purchasing and selling experience using yellow as theme color.

Target Market(s)

college students

Industry/Entity Type

Marketplace

Colors
ffc214
ffcf3e
fee18a
fff3d1

Requirements
Must have
• an improved UI look, flat and simple.
Nice to have
• alternative designs
Should not have
• a new function design for the app on the design

```html
<!DOCTYPE html>
<html lang="en">
<head>
<meta charset="utf-8">
<title>Tradolo – Product details</title>
<link href="https://fonts.googleapis.com/css2?family=Open+Sans:wght@400;600;700&display=swap" rel="stylesheet">
<style>
  :root {
    --page-bg: #f2f2f2;
    --bar-dark: #2b2f36;
    --tab-active: #3b4049;
    --band: rgba(44, 44, 46, 0.86);
    --yellow: #ffc214;
    --yellow-light: #ffcf3e;
    --heart-red: #ef4f5d;
    --text-white: #ffffff;
    --text-dark: #2a2a2a;
    --label-grey: #8e8e8e;
    --surface: #ffffff;
  }
  * { margin: 0; padding: 0; box-sizing: border-box; }
  html, body {
    width: 1200px; height: 1111px; overflow: hidden;
    background: var(--page-bg);
    font-family: "Open Sans", sans-serif;
  }
  .screen {
    position: absolute; left: 322px; top: 62px;
    width: 555px; height: 987px;
    background: var(--surface);
    overflow: hidden;
  }
  .status-bar {
    position: absolute; left: 0; top: 0; width: 100%; height: 32px;
    background: var(--bar-dark); color: var(--text-white);
    font-size: 17px; font-weight: 600;
  }
  .status-bar span { position: absolute; top: 3px; }
  .status-carrier { left: 8px; }
  .status-time { left: 0; width: 100%; text-align: center; }
  .status-battery { right: 10px; display: flex; align-items: center; gap: 6px; }
  .nav-bar {
    position: absolute; left: 0; top: 32px; width: 100%; height: 98px;
    background: var(--bar-dark);
  }
  .nav-title {
    position: absolute; left: 0; width: 100%; top: 28px; text-align: center;
    color: var(--text-white); font-size: 24px;
  }
  .nav-bar svg { position: absolute; }
  .hero {
    position: absolute; left: 0; top: 130px; width: 100%; height: 427px;
    background:
      linear-gradient(180deg, #cfd2d6 0%, #b8a58a 28%, #8a6a4e 55%, #6d5a6e 75%, #d9d4cf 100%);
  }
  .hero-title {
    position: absolute; left: 23px; top: 30px;
    color: var(--text-white); font-size: 34px; font-weight: 400;
  }
  .favourite {
    position: absolute; left: 465px; top: 23px; width: 66px; height: 66px;
    border-radius: 50%; background: var(--heart-red);
    display: flex; align-items: center; justify-content: center;
  }
  .seller-band {
    position: absolute; left: 0; bottom: 0; width: 100%; height: 112px;
    background: var(--band);
  }
  .seller-avatar {
    position: absolute; left: 22px; top: 25px; width: 60px; height: 60px;
    border-radius: 50%; background: linear-gradient(135deg, #e6d3c4, #8c6a55);
  }
  .seller-name {
    position: absolute; left: 95px; top: 22px;
    color: var(--text-white); font-size: 24px; font-weight: 600;
  }
  .seller-time {
    position: absolute; left: 95px; top: 61px;
    color: var(--text-white); font-size: 17px;
    display: flex; align-items: center; gap: 6px;
  }
  .send-button {
    position: absolute; left: 342px; top: 31px; width: 190px; height: 50px;
    border-radius: 25px; background: var(--yellow);
    color: var(--text-white); font-size: 17px; font-weight: 700;
    display: flex; align-items: center; justify-content: center;
    letter-spacing: 0.2px;
  }
  .details { position: absolute; left: 23px; top: 557px; right: 23px; }
  .field-label {
    color: var(--label-grey); font-size: 16px; font-weight: 600;
    letter-spacing: 0.3px; text-transform: uppercase;
  }
  .label-description { margin-top: 29px; }
  .description-text {
    margin-top: 14px; color: var(--text-dark); font-size: 24px; line-height: 32px;
  }
  .label-price { margin-top: 30px; }
  .price-value { margin-top: 16px; color: var(--text-dark); font-size: 24px; }
  .tab-bar {
    position: absolute; left: 0; bottom: 0; width: 100%; height: 87px;
    background: var(--bar-dark); display: flex;
  }
  .tab { flex: 1; display: flex; align-items: center; justify-content: center; }
  .tab-active { background: var(--tab-active); }
</style>
</head>
<body>
  <main class="screen">
    <div class="status-bar">
      <span class="status-carrier">●●●●● Campus</span>
      <span class="status-time">9:41 AM</span>
      <span class="status-battery">42%
        <svg width="30" height="14" viewBox="0 0 30 14"><rect x="1" y="1" width="25" height="12" rx="2" fill="none" stroke="#fff" stroke-width="1.5"/><rect x="3" y="3" width="10" height="8" fill="#fff"/><rect x="27" y="5" width="2" height="4" fill="#fff"/></svg>
      </span>
    </div>

    <header class="nav-bar">
      <svg style="left:34px;top:34px" width="14" height="26" viewBox="0 0 14 26"><path d="M12 2 L2 13 L12 24" fill="none" stroke="#fff" stroke-width="2"/></svg>
      <h1 class="nav-title" style="font-weight:400">Product details</h1>
      <svg style="left:444px;top:34px" width="28" height="28" viewBox="0 0 28 28" stroke="#fff" stroke-width="2" fill="none"><path d="M5 2v24M14 2v24M23 2v24M2 18h6M11 8h6M20 12h6"/></svg>
      <svg style="left:500px;top:34px" width="30" height="28" viewBox="0 0 30 28" stroke="#fff" stroke-width="2" fill="none"><path d="M2 6h24l-3 14H6z M26 6l2-4"/><path d="M6 24h18"/></svg>
    </header>

    <section class="hero" role="img" aria-label="Photo of a furnished living room with sofa, lamp and tall windows">
      <h2 class="hero-title">Quiet Garden</h2>
      <div class="favourite">
        <svg width="34" height="30" viewBox="0 0 24 22"><path d="M12 21 C4 14 1 10 1 6.5 A5.5 5.5 0 0 1 12 4 A5.5 5.5 0 0 1 23 6.5 C23 10 20 14 12 21z" fill="#fff"/></svg>
      </div>
      <div class="seller-band">
        <div class="seller-avatar" role="img" aria-label="Seller profile photo"></div>
        <p class="seller-name">Mara Ellison</p>
        <p class="seller-time">
          <svg width="18" height="18" viewBox="0 0 18 18" fill="none" stroke="#fff" stroke-width="1.5"><circle cx="9" cy="9" r="7.5"/><path d="M9 4.5V9h4"/></svg>
          Yesterday
        </p>
        <div class="send-button">SEND MESSAGE</div>
      </div>
    </section>

    <section class="details">
      <p class="field-label label-description">Description</p>
      <p class="description-text">This is a book can either painted and treasure, this is a book and can be used as a design reference book. At the same time.</p>
      <p class="field-label label-price">Price</p>
      <p class="price-value">$450.00</p>
    </section>

    <nav class="tab-bar">
      <div class="tab">
        <svg width="50" height="50" viewBox="0 0 50 50" fill="none" stroke="#fff" stroke-width="2"><path d="M25 4a21 20 0 1 1-12 36.5L5 44l3.5-8A20 20 0 0 1 25 4z"/><circle cx="17" cy="25" r="1.6" fill="#fff" stroke="none"/><circle cx="25" cy="25" r="1.6" fill="#fff" stroke="none"/><circle cx="33" cy="25" r="1.6" fill="#fff" stroke="none"/></svg>
      </div>
      <div class="tab tab-active">
        <svg width="46" height="42" viewBox="0 0 24 22"><path d="M12 21 C4 14 1 10 1 6.5 A5.5 5.5 0 0 1 12 4 A5.5 5.5 0 0 1 23 6.5 C23 10 20 14 12 21z" fill="var(--yellow)"/></svg>
      </div>
      <div class="tab">
        <svg width="56" height="50" viewBox="0 0 56 50"><rect x="2" y="2" width="52" height="34" rx="3" fill="#fff"/><rect x="7" y="12" width="42" height="14" rx="3" fill="var(--bar-dark)"/><text x="28" y="22.5" text-anchor="middle" font-family="Open Sans, sans-serif" font-size="8" font-weight="700" fill="#fff">RESERVED</text><path d="M28 36v10M20 46h16M22 40v6M34 40v6" stroke="#fff" stroke-width="2"/></svg>
      </div>
    </nav>
  </main>
</body>
</html>
```